Bramblewick Forage Business Cards

I need a business card with my logo, number, Facebook account, and some information about what I am selling. Green card with logo on the front. 555-214-8392 phone number, @bramblewickforage Facebook, •Orchardgrass Hay •Alfalfa Hay •Mixed Grass Hay , and “Premium Quality Hay” all written on the back.

Target Market(s)

Hay

Contact Information for Business Card

Phone number, Facebook, different types of hay.

Colors
00AB8E
00BBA5
67D7C9
C6EFE9
E9F9F6

```html
<!DOCTYPE html>
<html lang="en">
<head>
<meta charset="utf-8">
<title>Bramblewick Forage Business Cards</title>
<link rel="stylesheet" href="https://fonts.googleapis.com/css2?family=Noto+Sans:wght@400;600;700&family=Kaushan+Script&family=Arimo:wght@700&display=swap">
<style>
  :root {
    --brand-green: #00963f;
    --ink: #1a1a1a;
    --paper: #ffffff;
    --backdrop: #cfd0d1;
  }
  * { box-sizing: border-box; margin: 0; padding: 0; }
  html, body {
    width: 1187px;
    height: 1200px;
    overflow: hidden;
    background: var(--backdrop);
    font-family: "Noto Sans", sans-serif;
  }
  .card {
    position: absolute;
    left: 216px;
    width: 757px;
    height: 432px;
    border-radius: 18px;
    overflow: hidden;
  }
  .card--front {
    top: 122px;
    background: var(--brand-green);
    display: flex;
    align-items: center;
    justify-content: center;
    gap: 18px;
  }
  .front-mark {
    width: 44px;
    height: 44px;
    border-radius: 50%;
    background: var(--paper);
  }
  .front-name {
    color: var(--paper);
    font-weight: 600;
    font-size: 44px;
    letter-spacing: 0.5px;
  }
  .card--back {
    top: 644px;
    background: var(--paper);
  }
  .back-mark {
    position: absolute;
    left: 52px;
    top: 62px;
    width: 64px;
    height: 64px;
    border-radius: 50%;
    background: var(--brand-green);
  }
  .back-name {
    position: absolute;
    left: 134px;
    top: 60px;
    color: var(--ink);
    font-weight: 600;
    font-size: 36px;
    line-height: 1.2;
  }
  .tagline {
    position: absolute;
    left: 226px;
    top: 120px;
    color: var(--ink);
    font-weight: 700;
    font-size: 17px;
    letter-spacing: 0.8px;
  }
  .contact {
    position: absolute;
    left: 472px;
    top: 168px;
  }
  .contact-name {
    font-family: "Kaushan Script", cursive;
    color: var(--brand-green);
    font-size: 40px;
    line-height: 1.2;
    letter-spacing: 1px;
  }
  .contact-phone {
    margin-top: 12px;
    font-family: "Arimo", sans-serif;
    font-weight: 700;
    font-size: 34px;
    color: var(--ink);
    line-height: 1.1;
  }
  .contact-social {
    margin-top: 8px;
    display: flex;
    align-items: center;
    gap: 6px;
    font-size: 20px;
    color: var(--ink);
    letter-spacing: 0.6px;
  }
  .social-dot {
    width: 24px;
    height: 24px;
    border-radius: 50%;
    background: var(--brand-green);
  }
  .products {
    position: absolute;
    left: 100px;
    top: 355px;
    display: flex;
    gap: 14px;
    list-style: none;
    font-size: 19px;
    color: var(--ink);
    letter-spacing: 0.4px;
  }
  .products li {
    display: flex;
    align-items: center;
    gap: 8px;
  }
  .products li::before {
    content: "";
    width: 10px;
    height: 10px;
    border-radius: 50%;
    background: var(--brand-green);
  }
  .back-band {
    position: absolute;
    left: 0;
    bottom: 0;
    width: 100%;
    height: 13px;
    background: var(--brand-green);
  }
</style>
</head>
<body>
  <section class="card card--front">
    <span class="front-mark"></span>
    <span class="front-name">Bramblewick Forage</span>
  </section>

  <section class="card card--back">
    <span class="back-mark"></span>
    <h1 class="back-name">Bramblewick Forage</h1>
    <p class="tagline">“Premium Quality Hay”</p>

    <div class="contact">
      <p class="contact-name">Dale Whitcomb</p>
      <p class="contact-phone">555-214-8392</p>
      <p class="contact-social"><span class="social-dot"></span>@bramblewickforage</p>
    </div>

    <ul class="products">
      <li>Orchardgrass Hay</li>
      <li>Alfalfa Hay</li>
      <li>Mixed Grass Hay</li>
    </ul>

    <div class="back-band"></div>
  </section>
</body>
</html>
```